MRT Property - Business Cards

Looking for a business card & general letterhead, signage etc design for our new logo.

Colours:
000a20
0056a2
00b5ef
0088ce
68cef2

Fonts:
Poppins
Karla

Please keep look and feel of new brand - example in the zip package I sent.

```html
<!DOCTYPE html>
<html lang="en">
<head>
<meta charset="utf-8">
<title>MRT Property – Business Card</title>
<link rel="stylesheet" href="https://fonts.googleapis.com/css2?family=Poppins:wght@300;400;600;700&display=swap">
<style>
  :root {
    --ink: #000a20;
    --navy: #0056a2;
    --mid: #0088ce;
    --sky: #00b5ef;
    --pale: #68cef2;
    --deep: #00449a;
    --stage: #2b2b2d;
    --paper: #ffffff;
  }
  * { margin: 0; padding: 0; box-sizing: border-box; }
  html, body { width: 1200px; height: 1028px; overflow: hidden; }
  body {
    background: var(--stage);
    font-family: "Poppins", sans-serif;
    position: relative;
  }
  .card {
    position: absolute;
    left: 310px;
    width: 579px;
    height: 331px;
    border-radius: 24px;
    overflow: hidden;
  }
  .card-front { top: 165px; background: var(--paper); }
  .card-back { top: 532px; background: var(--navy); }

  .holder { position: absolute; left: 28px; top: 26px; }
  .holder-name {
    font-weight: 700;
    font-size: 26px;
    line-height: 1;
    letter-spacing: 0.3px;
    color: var(--navy);
  }
  .holder-name .surname { color: var(--mid); }
  .holder-role {
    font-weight: 300;
    font-size: 15.5px;
    color: var(--ink);
    margin-top: 2px;
  }

  .brand-front {
    position: absolute;
    right: 28px;
    top: 44px;
    font-weight: 600;
    font-size: 30px;
    color: var(--navy);
    line-height: 1;
  }

  .divider {
    position: absolute;
    left: 28px;
    right: 28px;
    top: 221px;
    height: 1px;
    background: var(--mid);
  }

  .contact {
    position: absolute;
    left: 28px;
    top: 236px;
    list-style: none;
    font-weight: 300;
    font-size: 15.5px;
    line-height: 19px;
    color: var(--ink);
  }
  .contact li { display: flex; align-items: center; gap: 4px; }
  .contact svg { width: 10px; height: 10px; flex: none; }

  .address {
    position: absolute;
    right: 28px;
    top: 245px;
    text-align: right;
    font-weight: 300;
    font-size: 15.5px;
    line-height: 19px;
    color: var(--ink);
  }

  .footer-band { position: absolute; left: 0; bottom: 0; width: 579px; height: 30px; }

  .brand-back {
    position: absolute;
    left: 0; right: 0;
    top: 132px;
    text-align: center;
    font-weight: 600;
    font-size: 58px;
    line-height: 1;
    color: var(--deep);
  }
</style>
</head>
<body>

<section class="card card-front" aria-label="Business card front">
  <div class="holder">
    <h1 class="holder-name">DANA <span class="surname">WHITLOCK</span></h1>
    <p class="holder-role">Founder &amp; Principal</p>
  </div>

  <div class="brand-front">MRT Property</div>

  <div class="divider"></div>

  <ul class="contact">
    <li>
      <svg viewBox="0 0 10 10" aria-hidden="true"><path d="M2 1 L3.5 1 L4 3 L3 3.8 Q4 6 6.2 7 L7 6 L9 6.5 L9 8 Q8.5 9 7.5 9 Q2 8 1 2.5 Q1 1.5 2 1Z" fill="none" stroke="var(--navy)" stroke-width="0.9"/></svg>
      +1- 415-555-0192
    </li>
    <li>
      <svg viewBox="0 0 10 10" aria-hidden="true"><rect x="0.8" y="2" width="8.4" height="6" fill="none" stroke="var(--navy)" stroke-width="0.9"/><path d="M0.8 2 L5 5.5 L9.2 2" fill="none" stroke="var(--navy)" stroke-width="0.9"/></svg>
      info@mrtproperty.com
    </li>
    <li>
      <svg viewBox="0 0 10 10" aria-hidden="true"><circle cx="5" cy="5" r="4.2" fill="none" stroke="var(--navy)" stroke-width="0.9"/><ellipse cx="5" cy="5" rx="1.8" ry="4.2" fill="none" stroke="var(--navy)" stroke-width="0.8"/><path d="M0.8 5 H9.2 M1.5 3 H8.5 M1.5 7 H8.5" stroke="var(--navy)" stroke-width="0.7"/></svg>
      www.mrtproperty.com
    </li>
  </ul>

  <address class="address" style="font-style:normal">
    4820 North Maple Avenue<br>
    #12, Suite Riverside Park
  </address>

  <svg class="footer-band" viewBox="0 0 579 30" aria-hidden="true">
    <path d="M0 20 H300 Q325 20 340 10 Q352 6 365 6 H579 V30 H0Z" fill="var(--navy)"/>
    <path d="M0 17 H303 Q308 17 304 19.5 H0Z" fill="var(--sky)"/>
    <path d="M0 19.5 H304 Q300 21.5 296 22 H0Z" fill="var(--paper)"/>
  </svg>
</section>

<section class="card card-back" aria-label="Business card back">
  <div class="brand-back">MRT Property</div>
</section>

</body>
</html>
```